Sci Fi/ Secret Agent Author needs website design!

My name is Lark Whitby and I am an author. I require a site that can provide information about myself and my books and other works.

I would like it to have a Home, blog function, (about the) books/series section so people can visit another section and read about each individual book that's going to be released. A resources page, a Store, social media links and ability to load/embed videos from clipvane and other.

I write mild scifi/thriller/conspiracy/secret government type novels. -At the moment-. The series follows a strong female lead that is an agent with a secret organisation in a classified military installation.

The theme would be professional yet possibly show this element.

/military fiction/thriller/fantasy/Sci fi/ femme-fatal, readers. Mostly females, age 18-60
Novel readers

5+ page

• Would like designers to follow brief. :)
• My budget includes all the pages I will need;
• eg home, blog, resources, store, ability to pay with coinpouch and Credit Cards
• , ability to have trailers from clipvane etc. Must have links to the social media mentioned in the brief.
• use of the colours I have suggested. electric/indigo purple, fuschia highlights , dark greys
• as I will possibly base branding for social media ETC on the look of your website design and colour scheme.
• Ability for trailer on front page??
• Should not be too cluttered. (But I am open to all ideas)

```html
<!DOCTYPE html>
<html lang="en">
<head>
<meta charset="utf-8">
<title>Lark Whitby — Author</title>
<link href="https://fonts.googleapis.com/css2?family=Arvo&family=Open+Sans:wght@400;600;700&display=swap" rel="stylesheet">
<style>
:root{
  --purple:#7a0dbf;
  --purple-field:#9a3fd3;
  --nav-active:#d8d0e0;
  --ink:#222;
  --body:#555;
  --white:#fff;
  --footer:#0d0b10;
  --footer-text:#e6e6e6;
  --rule:#2a2730;
}
*{box-sizing:border-box;margin:0;padding:0}
html,body{width:856px;height:1200px;overflow:hidden}
body{position:relative;background:var(--white);font-family:"Open Sans",sans-serif;color:var(--body)}
.abs{position:absolute}
h1,h2,h3{font-weight:400}

/* top nav */
.topnav{left:0;top:0;width:856px;height:30px;background:var(--purple);z-index:2}
.topnav ul{list-style:none;display:flex;position:absolute;left:59px;top:0;height:30px}
.topnav li{font-size:9.5px;color:var(--white);padding:0 12px;line-height:30px}
.topnav li.active{background:var(--nav-active);color:var(--purple)}
.social-dots{left:693px;top:11px;display:flex;gap:6px}
.social-dots span{width:8px;height:8px;border-radius:50%;background:var(--white);opacity:.9}
.cart{left:767px;top:6px;width:18px;height:18px;border-radius:50%;background:var(--white)}

.site-title{left:0;top:50px;width:856px;text-align:center;font-family:"Arvo",serif;font-size:33px;line-height:40px;color:var(--ink);letter-spacing:1px}

/* hero */
.hero{left:0;top:108px;width:856px;height:294px;background:linear-gradient(90deg,#4a3a30 0%,#6b4e3a 30%,#3a2a22 55%,#2a1d18 100%)}
.hero-title{left:70px;top:186px;font-size:34px;line-height:36px;color:var(--white);font-variant:small-caps;letter-spacing:1px}
.hero-text{left:71px;top:231px;width:430px;font-size:9.3px;line-height:22.6px;color:#eee}
.hero-meta{left:71px;top:310px;font-size:9.3px;line-height:12px;color:#eee;display:flex;gap:19px}
.hero-meta b{font-weight:600}
.book{left:532px;top:164px;width:126px;height:182px;background:linear-gradient(160deg,#c99a52,#6b3b1a 60%,#2a1508);box-shadow:4px 4px 0 #7a1020}
.book-credit{left:594px;top:324px;font-size:8px;color:var(--white)}
.arrow{width:14px;height:20px;top:245px}
.dots{left:400px;top:372px;display:flex;gap:5px}
.dots span{width:7px;height:7px;border-radius:50%;background:var(--white)}
.dots span.on{background:var(--purple)}

/* about */
.about-title{left:70px;top:470px;font-size:33px;line-height:40px;font-weight:600;color:var(--ink);font-variant:small-caps;letter-spacing:1px}
.about-text{left:70px;top:516px;width:382px;font-size:9.3px;line-height:22.6px;color:var(--body)}
.about-text p+p{margin-top:3px}
.video{left:483px;top:471px;width:303px;height:206px;background:linear-gradient(180deg,#5c6a3a,#4f6a2a 45%,#8a6a42 75%,#a07a4e)}
.play{left:618px;top:560px;width:32px;height:26px}

/* signup */
.signup{left:0;top:745px;width:856px;height:177px;background:var(--purple)}
.envelope{left:137px;top:785px;width:50px;height:40px}
.signup-title{left:197px;top:780px;font-size:30px;line-height:36px;font-weight:600;color:var(--white);font-variant:small-caps;letter-spacing:1px}
.email-field{left:198px;top:844px;width:415px;height:38px;background:var(--purple-field);border:1px solid #c58ae8;font-size:9.5px;color:#f0e6f7;padding:0 17px;line-height:36px}
.subscribe{left:617px;top:844px;width:103px;height:38px;background:#1c1a20;color:var(--white);font-size:10.5px;font-weight:700;letter-spacing:.8px;text-align:center;line-height:38px}

/* footer */
.footer{left:0;top:922px;width:856px;height:278px;background:var(--footer)}
.f-head{top:960px;font-size:12.5px;line-height:16px;font-weight:600;color:var(--white)}
.f-list{list-style:none;font-size:8.8px;color:var(--footer-text)}
.f-list li{height:24.4px;display:flex;align-items:center;gap:9px}
.chev{font-size:8px;font-weight:700}
.contact li{height:auto;align-items:flex-start;margin-bottom:10px;line-height:16.5px}
.contact li span{width:150px}
.contact svg{flex:none;margin-top:4px}
.social li{height:30.5px}
.ring{width:24px;height:24px;border-radius:50%;border:1px solid #bbb;flex:none;display:flex;align-items:center;justify-content:center}
.ring i{width:7px;height:7px;border-radius:50%;background:var(--white)}
.rule{left:70px;top:1146px;width:716px;height:1px;background:var(--rule)}
.copyright{left:0;top:1168px;width:856px;text-align:center;font-size:9px;color:var(--footer-text)}
</style>
</head>
<body>

<nav class="topnav abs">
  <ul>
    <li class="active">Home</li><li>About the book</li><li>Resources</li><li>Store</li><li>Blog</li><li>Contact us</li>
  </ul>
  <div class="social-dots abs"><span></span><span></span><span></span><span></span><span></span></div>
  <div class="cart abs"></div>
</nav>

<h1 class="site-title abs">Lark Whitby</h1>

<section class="hero abs" role="img" aria-label="Misty forest at dusk with a shadowy figure among the trees"></section>
<h2 class="hero-title abs">Conspiracy Novels</h2>
<p class="hero-text abs">Nor again is there anyone who loves or pursues or desires to obtain pain of itself, because it is pain, but because occasionaln which toil and pain can procat plea a trivial example, wever undertakes lat beborious physical exercise..</p>
<div class="hero-meta abs"><span>&#9638; 25 January 2017</span><b>Minima veniam</b></div>
<div class="book abs" role="img" aria-label="Book cover: a woman reading by lamplight"></div>
<div class="book-credit abs">- Lark Whitby</div>
<svg class="arrow abs" style="left:21px" viewBox="0 0 14 20"><path d="M10 3 L4 10 L10 17" stroke="#fff" stroke-width="2" fill="none"/></svg>
<svg class="arrow abs" style="left:821px" viewBox="0 0 14 20"><path d="M4 3 L10 10 L4 17" stroke="#fff" stroke-width="2" fill="none"/></svg>
<div class="dots abs"><span class="on"></span><span></span><span></span><span></span><span></span></div>

<h2 class="about-title abs">About Lark Whitby</h2>
<div class="about-text abs">
  <p>Nemo enim ipsam voluptatem quia voluptas sit aspernatur aut odit aut fugit, sed quia consequuntur magni dolores eos qui ratione voluptatem sequi nesciunt. Neque porro quisquam est, qui dolorem ipsum quia dolor sit amet, consectetur, adipisci velit, sed quia non numquam eidunt ut labore et dolore magnam...</p>
  <p>aliquam quaerat voluptatem. Ut enim ad minima veniam, quis nostrum exercitationem ullam corporis suscipit laboriosam, nisi ut aliquid ex ea commodi consequatur? Quis autem vel eum iure reprehenderi....</p>
</div>
<div class="video abs" role="img" aria-label="Trailer video: the author writing at a typewriter outdoors"></div>
<svg class="play abs" viewBox="0 0 32 26"><circle cx="16" cy="13" r="12" fill="#fff" opacity=".9"/><path d="M13 8 L21 13 L13 18 Z" fill="var(--purple)"/></svg>

<section class="signup abs"></section>
<svg class="envelope abs" viewBox="0 0 50 40"><path d="M2 8 L46 2 L48 34 L4 38 Z" fill="#fff"/><path d="M2 8 L26 22 L46 2 M4 38 L20 20 M48 34 L30 20" stroke="var(--purple)" stroke-width="2" fill="none"/></svg>
<h2 class="signup-title abs">Sign up For Update Email</h2>
<div class="email-field abs">Enter Email.....</div>
<div class="subscribe abs">SUBSCRIBE</div>

<footer class="footer abs"></footer>
<h3 class="f-head abs" style="left:71px">CONTACT US</h3>
<h3 class="f-head abs" style="left:274px">QUICK LINKS</h3>
<h3 class="f-head abs" style="left:426px">MY ACCOUNT</h3>
<h3 class="f-head abs" style="left:582px">STAY CONNECTED</h3>

<ul class="f-list contact abs" style="left:71px;top:992px;width:190px">
  <li><svg width="9" height="9" viewBox="0 0 10 10"><path d="M2 1 L4 1 L5 3.5 L3.6 4.5 Q4.6 6.5 6 6.6 L7 5.2 L9.2 6.2 L9.2 8.2 Q4 9.5 1 2.5 Z" fill="#fff"/></svg><span>(555)-214-3087</span></li>
  <li><svg width="10" height="8" viewBox="0 0 10 8"><rect width="10" height="8" fill="#fff"/><path d="M0 0 L5 4 L10 0" stroke="#0d0b10" fill="none"/></svg><span>hello@larkwhitby.site</span></li>
  <li><svg width="8" height="10" viewBox="0 0 8 10"><path d="M4 10 L1 5 A3.5 3.5 0 1 1 7 5 Z" fill="#fff"/><circle cx="4" cy="3.5" r="1.3" fill="#0d0b10"/></svg><span>45BC,Lorem ipsum dolor numquam sit amet adipisci velit sed numquam eius</span></li>
</ul>

<ul class="f-list abs" style="left:274px;top:986px">
  <li><span class="chev">&raquo;</span>Home</li><li><span class="chev">&raquo;</span>About the book</li><li><span class="chev">&raquo;</span>Resources</li><li><span class="chev">&raquo;</span>Store</li><li><span class="chev">&raquo;</span>Contact Us</li>
</ul>
<ul class="f-list abs" style="left:426px;top:986px">
  <li><span class="chev">&raquo;</span>Log In</li><li><span class="chev">&raquo;</span>Account</li><li><span class="chev">&raquo;</span>Register</li><li><span class="chev">&raquo;</span>View Basket</li><li><span class="chev">&raquo;</span>Terms &amp; Conditions</li>
</ul>
<ul class="f-list social abs" style="left:583px;top:991px">
  <li><span class="ring"><i></i></span>Friendwall</li><li><span class="ring"><i></i></span>Chirpline</li><li><span class="ring"><i></i></span>Snapframe</li><li><span class="ring"><i></i></span>Clipvane</li>
</ul>
<ul class="f-list social abs" style="left:691px;top:991px">
  <li><span class="ring"><i></i></span>Pinboardly</li>
</ul>

<div class="rule abs"></div>
<p class="copyright abs">&copy; copyright 2017&nbsp; Lark Whitby.All Rights Reserved</p>

</body>
</html>
```